Venture Capital Firm Needs Website Redesign

We need a bold revamp of our website (https://halverine.vc/)
which at the moment looks washed out. We want a crisp, fresh and unique look. Feel free to keep as much or as little content in the site. The only thing we need to keep is a team section. The site should convey a clear distinction between our 3 product lines: Venture Capital, Private Credit, and Crypto. Two versions of our logo are attached and they should not change. For design inspirations, we like http://www.9plm.com/ for a more simple site and for a more built out site we like http://bluetorch.com/

Updates
Industry/Entity Type
Investment
Coding
Coded - Design and coding required
Number of Pages Required
1 page
Font styles to use
Colors
Designer to choose colors to be used in the design.
Requirements
Must have
- - Clear distinction between our 3 product lines: Venture Capital, Private Credit
- - Team section

Nice to have
- Some really creative aspect like http://www.9plm.com/ has with the distinction between first, second, and third kind

```html
<!DOCTYPE html>
<html lang="en">
<head>
<meta charset="utf-8">
<title>Halverine</title>
<link href="https://fonts.googleapis.com/css2?family=Poppins:wght@300;400;500;600;700&display=swap" rel="stylesheet">
<style>
:root{
  --green:#8ba52a;
  --green-dark:#6f8a1c;
  --green-pale:#e6edcf;
  --green-wash:#f1f5e3;
  --ink:#2b2b2b;
  --text:#555;
  --muted:#888;
  --grey-bg:#ececec;
  --cta-bg:#eef1f6;
  --white:#fff;
}
*{margin:0;padding:0;box-sizing:border-box}
html,body{width:1200px;height:3309px;overflow:hidden}
body{font-family:'Poppins',sans-serif;color:var(--ink);background:var(--white);position:relative}
.abs{position:absolute}
a{color:inherit;text-decoration:none}

/* header */
.brand{position:absolute;display:flex;align-items:center;gap:10px;font-weight:500;letter-spacing:.5px;color:var(--ink)}
.brand-mark{width:44px;height:44px;border:2px solid var(--ink);border-radius:50%}
.site-header .brand{left:160px;top:33px;font-size:26px}
.nav{position:absolute;left:507px;top:46px;display:flex;gap:38px;font-size:12.5px;font-weight:500;letter-spacing:.6px}

/* hero */
.hero{position:absolute;left:0;top:0;width:1200px;height:660px;overflow:hidden;
  background:linear-gradient(180deg,#fff 0%,#fbfcf6 60%,#f3f6e8 100%)}
.hero-wave{position:absolute;left:0;top:0}
.hero-title{position:absolute;left:160px;top:228px;font-size:44px;font-weight:600;color:var(--green);letter-spacing:.5px}
.hero-tagline{position:absolute;left:160px;top:292px;width:420px;font-size:28px;line-height:1.36;font-weight:400}
.hero-art{position:absolute;left:591px;top:121px;width:545px;height:430px;
  background:
    radial-gradient(ellipse at 55% 70%,rgba(139,165,42,.85) 0%,rgba(139,165,42,.55) 35%,rgba(139,165,42,0) 65%),
    linear-gradient(165deg,#f7f7f7 0%,#e6e6e6 35%,#c9d89a 62%,#8ba52a 85%,#5f7a16 100%);
  clip-path:polygon(0 16%,55% 0,100% 14%,100% 74%,50% 100%,0 80%)}
.slider-dots{position:absolute;left:512px;top:598px;display:flex;gap:6px}
.slider-dots i{display:block;width:40px;height:5px;background:#555;border-radius:2px}
.slider-dots i.on{background:var(--white);border:1px solid #999}

/* sections */
.section-rule{width:112px;height:3px;background:var(--green)}
.section-title{font-size:28px;font-weight:400;letter-spacing:1.5px}
.section-title span{color:var(--green)}
.section-copy{font-size:12.5px;line-height:2;color:var(--text)}

.vc{position:absolute;left:0;top:660px;width:1200px;height:454px;background:linear-gradient(180deg,#fff 0%,var(--grey-bg) 100%)}
.portfolio-badge{position:absolute;width:140px;height:140px;border-radius:50%;border:3px solid #777;background:#fafafa;
  display:flex;align-items:center;justify-content:center;font-size:19px;color:#666}
.portfolio-badge::before,.portfolio-badge::after{content:"";position:absolute;top:62px;width:12px;height:12px;border-radius:50%;background:#777}
.portfolio-badge::before{left:-8px}
.portfolio-badge::after{right:-8px}

.credit{position:absolute;left:0;top:1114px;width:1200px;height:585px;background:var(--white);overflow:hidden}
.credit-art{position:absolute;left:684px;top:110px;width:342px;height:243px;border-radius:48% 52% 40% 60%/55% 45% 55% 45%;
  background:linear-gradient(135deg,#d6e49a 0%,#a8c43c 60%,#8ba52a 100%)}
.partner{position:absolute;top:478px;font-size:26px;font-weight:600;color:#6c6c6c;display:flex;align-items:center;gap:10px}
.partner .sq{width:30px;height:30px;background:#7a7a7a}
.partner .ci{width:30px;height:30px;border-radius:50%;background:#7a7a7a}

.crypto{position:absolute;left:0;top:1699px;width:1200px;height:489px;background:linear-gradient(135deg,#e9e9e9 0%,#dedede 100%)}
.chart-card{position:absolute;left:161px;top:70px;width:441px;height:353px;background:#efefef;box-shadow:0 1px 6px rgba(0,0,0,.08)}

.team{position:absolute;left:0;top:2188px;width:1200px;height:612px;overflow:hidden;background:linear-gradient(180deg,#fff 30%,#eef3dc 100%)}
.member{position:absolute;top:172px;width:220px;text-align:center}
.member-photo{width:165px;height:165px;margin:0 auto;border-radius:50%;border:4px solid #c9d3a8;position:relative;
  background:
    radial-gradient(ellipse 34% 30% at 50% 40%,#c9a58a 0%,#b48d72 60%,rgba(180,141,114,0) 100%),
    linear-gradient(180deg,#f1f1f1 0%,#e2e2e2 55%,#3c3f44 78%,#2a2c30 100%)}
.member-photo.warm{background:
    radial-gradient(ellipse 34% 30% at 50% 42%,#d8b49a 0%,#c39a7e 60%,rgba(195,154,126,0) 100%),
    linear-gradient(180deg,#ececec 0%,#dcdcdc 50%,#5a4a40 75%,#2f2a28 100%)}
.member-photo::before,.member-photo::after{content:"";position:absolute;top:72px;width:14px;height:14px;border-radius:50%;background:#c9d3a8}
.member-photo::before{left:-13px}.member-photo::after{right:-13px}
.member-name{margin-top:16px;font-size:16px;font-weight:600}
.member-role{font-size:11.5px;color:var(--text)}
.btn{position:absolute;display:flex;align-items:center;justify-content:center;font-size:11.5px;font-weight:600;letter-spacing:.8px}
.btn-solid{background:var(--green-dark);color:var(--white)}
.btn-outline{border:2px solid var(--green);color:var(--green);background:var(--white)}

.cta{position:absolute;left:0;top:2800px;width:1200px;height:178px;background:var(--cta-bg)}
.cta-title{position:absolute;left:159px;top:66px;font-size:22px;color:var(--green);font-weight:400}
.cta-sub{position:absolute;left:159px;top:106px;font-size:14px;color:var(--text)}

.footer{position:absolute;left:0;top:2978px;width:1200px;height:331px;background:linear-gradient(180deg,#f6f7fa 0%,#eceef3 100%)}
.footer .brand{left:160px;top:46px;font-size:20px}
.footer .brand-mark{width:38px;height:38px}
.footer-contact{position:absolute;left:160px;top:106px;font-size:11.5px;line-height:1.85;color:#444}
.footer-social{position:absolute;left:160px;top:200px;display:flex;gap:10px}
.footer-social i{width:13px;height:13px;border-radius:50%;background:#999;display:block}
.footer-col{position:absolute;top:44px;font-size:11px;color:#555}
.footer-col h4{font-size:12px;font-weight:600;letter-spacing:1px;color:var(--ink);margin-bottom:16px}
.footer-col li{list-style:none;line-height:21px}
.copyright{position:absolute;left:0;top:282px;width:1200px;text-align:center;font-size:10.5px;color:#444;letter-spacing:.3px}
</style>
</head>
<body>

<section class="hero">
  <svg class="hero-wave" width="1200" height="660" viewBox="0 0 1200 660" aria-hidden="true">
    <path d="M0 640 C250 560 420 620 600 650 C800 680 1000 600 1200 560 L1200 660 L0 660Z" fill="#e9f0d2"/>
    <path d="M0 120 C120 220 140 420 40 560" fill="none" stroke="#edf2de" stroke-width="40"/>
    <path d="M0 60 C190 200 210 470 60 640" fill="none" stroke="#f1f5e6" stroke-width="36"/>
    <circle cx="15" cy="195" r="50" fill="#dde7bc"/>
    <circle cx="1068" cy="590" r="80" fill="#dfe8c1"/>
    <circle cx="1130" cy="15" r="100" fill="#eef3dd"/>
  </svg>
  <header class="site-header">
    <div class="brand"><div class="brand-mark"></div><span>HALVERINE</span></div>
    <nav class="nav"><a>VENTURE</a><a>PRIVATE CREDIT</a><a>CRYPTO</a><a>ABOUT US</a><a>TEAM</a><a>BLOG</a></nav>
  </header>
  <h1 class="hero-title">HALVERINE</h1>
  <p class="hero-tagline">Operates at the intersection of technology and novel asset classes.</p>
  <div class="hero-art" role="img" aria-label="Isometric illustration of an office with people working at desks on a green floor"></div>
  <div class="slider-dots"><i></i><i></i><i class="on"></i><i></i></div>
</section>

<section class="vc">
  <div class="portfolio-badge" style="left:158px;top:62px">Northmark</div>
  <div class="portfolio-badge" style="left:322px;top:62px">tilecraft</div>
  <div class="portfolio-badge" style="left:158px;top:213px">pathnest</div>
  <div class="portfolio-badge" style="left:322px;top:213px">Ledgerline</div>
  <div class="section-rule abs" style="left:617px;top:86px"></div>
  <h2 class="section-title abs" style="left:617px;top:108px">VENTURE <span>CAPITAL</span></h2>
  <p class="section-copy abs" style="left:620px;top:164px;width:380px">We invest in early-stage startups led by founders who are passionate and knowledgeable about the markets they serve. We have our own software developers and product managers. We work with the founders in our portfolio to help them bring products to market, earning equity for this work and for the cash we invest in their companies.</p>
</section>

<section class="credit">
  <svg class="abs" style="left:960px;top:60px" width="240" height="520" aria-hidden="true">
    <path d="M240 0 C60 80 40 420 240 520" fill="none" stroke="#eef3df" stroke-width="34"/>
    <path d="M240 70 C120 140 110 380 240 450" fill="none" stroke="#f3f6e9" stroke-width="30"/>
  </svg>
  <div class="section-rule abs" style="left:159px;top:144px"></div>
  <h2 class="section-title abs" style="left:159px;top:166px">PRIVATE <span>CREDIT</span></h2>
  <p class="section-copy abs" style="left:162px;top:220px;width:390px">Halverine Private Credit provides capital to lending businesses that are focused on using technology to establish new credit markets, create new credit products or dramatically re-invent an existing form of credit. We believe that the pioneers who build something truly different in a credit market will create the most sustainable business models.</p>
  <div class="credit-art" role="img" aria-label="Illustration of two payment cards on a green shape"></div>
  <svg class="abs" style="left:684px;top:336px" width="330" height="12" aria-hidden="true"><line x1="0" y1="6" x2="330" y2="6" stroke="#333" stroke-width="3"/></svg>
  <div class="partner" style="left:375px">RAVELO<span class="sq"></span></div>
  <div class="partner" style="left:575px"><span class="ci"></span></div>
  <div class="partner" style="left:668px;font-weight:500">BRIGHTLEDGER</div>
</section>

<section class="crypto">
  <div class="chart-card">
    <svg width="441" height="353" viewBox="0 0 441 353" font-family="Poppins, sans-serif" aria-label="Line chart of cumulative index growth versus benchmark">
      <text x="220" y="26" font-size="9" text-anchor="middle" fill="#333">HCI™ Cumulative Growth</text>
      <circle cx="120" cy="50" r="6" fill="#b5c21e"/><text x="130" y="53" font-size="8" fill="#333">HCI™ (1236.48%)</text>
      <circle cx="222" cy="50" r="6" fill="#111"/><text x="232" y="53" font-size="8" fill="#333">Benchmark (717.41%)</text>
      <g font-size="8" fill="#444" text-anchor="end">
        <text x="32" y="323">0</text><text x="32" y="290">500</text><text x="32" y="257">1000</text><text x="32" y="224">1500</text>
        <text x="32" y="192">2000</text><text x="32" y="159">2500</text><text x="32" y="126">3000</text><text x="32" y="93">3500</text>
      </g>
      <line x1="40" y1="320" x2="415" y2="320" stroke="#bbb"/>
      <polyline fill="none" stroke="#b5c21e" stroke-width="2.5" points="45,320 71,319 97,318 123,316 149,312 175,304 201,292 227,300 253,284 279,277 305,287 331,267 357,156 383,116 409,235"/>
      <polyline fill="none" stroke="#111" stroke-width="2.5" points="45,320 71,320 97,319 123,318 149,316 175,312 201,307 227,310 253,300 279,297 305,304 331,290 357,208 383,254 409,271"/>
      <g font-size="8" fill="#444" text-anchor="middle">
        <text x="45" y="336">Jan</text><text x="71" y="336">Feb</text><text x="97" y="336">Mar</text><text x="123" y="336">Apr</text><text x="149" y="336">May</text>
        <text x="175" y="336">Jun</text><text x="201" y="336">Jul</text><text x="227" y="336">Aug</text><text x="253" y="336">Sep</text><text x="279" y="336">Oct</text>
        <text x="305" y="336">Nov</text><text x="331" y="336">Dec</text><text x="357" y="336">Jan</text><text x="383" y="336">Feb</text><text x="409" y="336">Mar</text>
      </g>
    </svg>
  </div>
  <div class="section-rule abs" style="left:655px;top:125px"></div>
  <h2 class="section-title abs" style="left:655px;top:147px">CRYPTO</h2>
  <p class="section-copy abs" style="left:658px;top:202px;width:390px">The Halverine Crypto Index tracks the top 15 cryptocurrencies weighted by market cap and rebalanced twice a month. We believe this is the simplest and most cost effective way to obtain cryptocurrency exposure. Our process has been designed by experts from financial services and cryptocurrency industries.</p>
</section>

<section class="team">
  <svg class="abs" style="left:0;top:0" width="1200" height="612" aria-hidden="true">
    <path d="M820 0 C880 120 1100 130 1200 60 L1200 0Z" fill="#e6edcf"/>
    <circle cx="-5" cy="183" r="50" fill="#e4ebca"/>
  </svg>
  <h2 class="section-title abs" style="left:0;top:80px;width:1200px;text-align:center">OUR TEAM</h2>
  <div class="member" style="left:148px"><div class="member-photo" role="img" aria-label="Portrait photo of Omar Fenwick"></div><div class="member-name">Omar Fenwick</div><div class="member-role">Partner</div></div>
  <div class="member" style="left:375px"><div class="member-photo warm" role="img" aria-label="Portrait photo of Rohan Ellisworth"></div><div class="member-name">Rohan Ellisworth</div><div class="member-role">Partner</div></div>
  <div class="member" style="left:600px"><div class="member-photo" role="img" aria-label="Portrait photo of Tariq Delmont"></div><div class="member-name">Tariq Delmont</div><div class="member-role">Partner</div></div>
  <div class="member" style="left:830px"><div class="member-photo warm" role="img" aria-label="Portrait photo of Clara Whitfield"></div><div class="member-name">Clara Whitfield</div><div class="member-role">Community Manager</div></div>
  <a class="btn btn-solid" style="left:525px;top:442px;width:150px;height:42px">VIEW ALL TEAM ›</a>
</section>

<section class="cta">
  <svg class="abs" style="left:0;top:-60px" width="1200" height="80" aria-hidden="true">
    <path d="M0 60 C300 10 600 0 800 30 C950 50 1080 30 1200 10 L1200 80 L0 80Z" fill="#eef1f6"/>
    <circle cx="1020" cy="60" r="75" fill="#dfe8c2"/>
  </svg>
  <h3 class="cta-title">Ready to get started?</h3>
  <p class="cta-sub">Get in touch, or create an account.</p>
  <a class="btn btn-outline" style="left:750px;top:105px;width:152px;height:34px">CREATE ACCOUNT</a>
  <a class="btn btn-solid" style="left:907px;top:105px;width:130px;height:34px">CONTACT US</a>
</section>

<footer class="footer">
  <div class="brand"><div class="brand-mark"></div><span>HALVERINE</span></div>
  <div class="footer-contact">info@halverine.vc<br>218 Larkspur Avenue, Suite 405<br>Brookvale, NY 10987</div>
  <div class="footer-social"><i></i><i></i><i></i><i></i><i></i></div>
  <div class="footer-col" style="left:435px"><h4>LINKS</h4><ul><li>Payments</li><li>Subscriptions</li><li>Connect</li><li>Pricing</li><li>Works with Us</li><li>Global</li></ul></div>
  <div class="footer-col" style="left:591px"><h4>DEVELOPERS</h4><ul><li>Documentation</li><li>API reference</li><li>API status</li><li>Open source</li></ul></div>
  <div class="footer-col" style="left:788px"><h4>COMPANY</h4><ul><li>About</li><li>Customers</li><li>Jobs</li><li>Blog</li><li>Press</li></ul></div>
  <div class="footer-col" style="left:944px"><h4>RESOURCES</h4><ul><li>Support</li><li>Contact</li><li>Privacy &amp; terms</li></ul></div>
  <p class="copyright">© 2018 HALVERINE. ALL RIGHTS RESERVED. PRIVACY POLICY, TERMS AND CONDITIONS</p>
</footer>

</body>
</html>
```